Automotive eCommerce Business looking for a business card design

Looking for a clean and simple business card design. Our company name is "Brindle Auto" and we are a company specializing in the ecommerce sales of automotive parts, specifically for pick up trucks and large SUVs. Our company colours are red, black, and white.

Feel free to use the logo provided or create a new logo that you seem fit. Looking forward to your creative ideas!

Industry/Entity Type

Automotive

Contact Information for Business Card

We were thinking of a possibly two-sided design featuring just the logo and company name on one side, and personal information on the other side. Single sided designs will be considered as well.

Font styles to use
Serif
Sans Serif
Decorative

Colors
ec1f27
ffffff
000000

Requirements
Must have
• Space for employee's name, title, phone number and email address, along with the company address and website somewhere.

```html
<!DOCTYPE html>
<html lang="en">
<head>
<meta charset="utf-8">
<title>Brindle Auto Ltd – Business Card</title>
<link rel="stylesheet" href="https://fonts.googleapis.com/css2?family=Work+Sans:wght@400;500;600&display=swap">
<style>
  :root {
    --red: #ec1f27;
    --black: #000000;
    --white: #ffffff;
    --ink: #1c1c1c;
    --card-back: #161616;
    --silver: #b9b9b9;
    --stage: #e4e4e4;
  }
  * { box-sizing: border-box; margin: 0; padding: 0; }
  html, body {
    width: 1200px; height: 900px; overflow: hidden;
    background: var(--stage);
    font-family: "Work Sans", Arial, sans-serif;
  }
  .sheet {
    width: 1200px; height: 900px;
    display: flex; flex-direction: column; align-items: center; justify-content: center;
    gap: 40px;
  }
  .card {
    position: relative; width: 700px; height: 400px;
    border-radius: 22px; overflow: hidden;
  }
  /* Back side */
  .card--back {
    background: var(--card-back);
    display: flex; flex-direction: column; align-items: center; justify-content: center;
  }
  .back-name {
    color: var(--silver); font-weight: 600; font-size: 52px; letter-spacing: 8px;
    text-transform: uppercase;
  }
  .back-sub {
    color: var(--silver); font-weight: 600; font-size: 20px; letter-spacing: 22px;
    text-transform: uppercase; margin-top: 6px; padding-left: 22px;
  }
  /* Front side */
  .card--front { background: var(--white); }
  .brand {
    position: absolute; left: 40px; top: 40px;
    display: flex; align-items: center; gap: 14px;
  }
  .brand-mark { width: 22px; height: 22px; background: var(--red); }
  .brand-name {
    color: var(--red); font-weight: 600; font-size: 34px; letter-spacing: 4px;
    text-transform: uppercase; line-height: 1;
  }
  .divider {
    position: absolute; left: 200px; right: 40px; top: 214px;
    height: 2px; background: var(--red);
  }
  .person { position: absolute; right: 40px; top: 172px; text-align: right; }
  .person-name {
    color: var(--red); font-weight: 500; font-size: 30px; letter-spacing: 1px;
    text-transform: uppercase; line-height: 34px;
  }
  .person-title { color: var(--ink); font-size: 20px; margin-top: 10px; letter-spacing: 1px; }
  .contacts {
    position: absolute; left: 40px; top: 180px;
    list-style: none; font-size: 17px; color: var(--ink); line-height: 26px;
  }
  .contacts li { display: flex; align-items: center; gap: 10px; }
  .contacts svg { width: 12px; height: 12px; flex: none; }
  .contacts .accent { color: var(--red); }
  .footer-bands { position: absolute; left: 0; bottom: 0; width: 700px; height: 110px; }
</style>
</head>
<body>
<main class="sheet">
  <section class="card card--back" aria-label="Card back">
    <div class="back-name">Brindle</div>
    <div class="back-sub">Auto Ltd</div>
  </section>

  <section class="card card--front" aria-label="Card front">
    <div class="brand">
      <span class="brand-mark"></span>
      <span class="brand-name">Brindle Auto Ltd</span>
    </div>

    <ul class="contacts">
      <li>
        <svg viewBox="0 0 12 12"><path d="M3 1 L5 3.5 L4 5 Q5.5 7.5 7 8 L8.5 7 L11 9 L9.5 11 Q3 10 1 2.5 Z" fill="var(--red)"/></svg>
        555.014.2087
      </li>
      <li>
        <svg viewBox="0 0 12 12"><rect x="3" y="0.5" width="6" height="11" rx="1" fill="none" stroke="var(--red)" stroke-width="1.2"/><circle cx="6" cy="9.5" r="0.7" fill="var(--red)"/></svg>
        555.019.6634
      </li>
      <li>
        <svg viewBox="0 0 12 12"><rect x="0.8" y="2.5" width="10.4" height="7" fill="none" stroke="var(--red)" stroke-width="1.2"/><path d="M1 3 L6 7 L11 3" fill="none" stroke="var(--red)" stroke-width="1.2"/></svg>
        info@brindleautoltd.com
      </li>
      <li>
        <svg viewBox="0 0 12 12"><circle cx="6" cy="6" r="5" fill="none" stroke="var(--red)" stroke-width="1.2"/><path d="M1 6 H11 M6 1 Q3 6 6 11 M6 1 Q9 6 6 11" fill="none" stroke="var(--red)" stroke-width="1"/></svg>
        <span>www.<span class="accent">brindleautoltd</span>.com</span>
      </li>
    </ul>

    <div class="divider"></div>

    <div class="person">
      <div class="person-name">Marcus Ellery</div>
      <div class="person-title">Director</div>
    </div>

    <svg class="footer-bands" viewBox="0 0 700 110" preserveAspectRatio="none" aria-hidden="true">
      <path d="M0 18 L360 58 C400 62 410 72 440 76 L700 76 L700 110 L0 110 Z" fill="var(--red)"/>
      <path d="M0 4 L360 44 C390 47 400 54 420 58 L360 50 L0 12 Z" fill="var(--black)"/>
      <path d="M0 12 L360 52 L0 18 Z" fill="var(--white)"/>
    </svg>
  </section>
</main>
</body>
</html>
```